Veterinary Pylon

My veterinary clinic is not clearly visible from the street and I want to place a Pylon next to my driveway. I want a modern, elegant straight Design, the Photo shows the sheduled place. One can see the clinic on our Homepage: www.tailbright-vethaus.at
The last pictures are examples for pylones I like

Target Market(s)

the passing cars often miss my entry...I want to show where to turn left

Colors
3276b5
33a6d7
00a990

Requirements
Must have
• High value, simple elegance, size: 250cm (high) x 100cm (width)
Nice to have
• Our Logo, arrow(?)

A special Text is not necessary but this will be an option:

Biegen sie hier ab und wir biegen es wieder hin!
Should not have
• Too much Color, the colors I have chosen are the possible colors but it‘s not necessary to use them.

```html
<!DOCTYPE html>
<html lang="de">
<head>
<meta charset="utf-8">
<title>Tailbright Vethaus – Pylon</title>
<link href="https://fonts.googleapis.com/css2?family=Montserrat:wght@600;700&display=swap" rel="stylesheet">
<style>
  :root {
    --navy: #2b4a8c;
    --sky: #3cb4de;
    --white: #ffffff;
    --backdrop: #eef0f2;
  }
  * { margin: 0; padding: 0; box-sizing: border-box; }
  html, body {
    width: 818px;
    height: 1200px;
    overflow: hidden;
    background: var(--backdrop);
  }
  .pylon {
    position: absolute;
    left: 181px;
    top: 30px;
    width: 456px;
    height: 1140px;
    overflow: hidden;
    background: linear-gradient(180deg, var(--white) 0%, var(--white) 45%, #f1f8fd 58%, #f6fbfe 63%);
    box-shadow: 0 6px 18px rgba(0, 0, 0, 0.18);
    font-family: "Montserrat", Arial, sans-serif;
  }
  .brand {
    position: absolute;
    top: 58px;
    left: 0;
    width: 100%;
    display: flex;
    flex-direction: column;
    align-items: center;
  }
  .brand-dot {
    width: 200px;
    height: 200px;
    border-radius: 50%;
    background: var(--sky);
  }
  .brand-name {
    margin-top: 26px;
    color: var(--navy);
    font-weight: 700;
    font-size: 64px;
    line-height: 72px;
    text-align: center;
    letter-spacing: 0.5px;
  }
  .headline {
    position: absolute;
    top: 515px;
    left: 53px;
    right: 30px;
    color: var(--navy);
    font-weight: 700;
    font-size: 41px;
    line-height: 49px;
    letter-spacing: 0.2px;
  }
  .photo {
    position: absolute;
    top: 700px;
    left: 0;
    width: 100%;
    height: 440px;
    background:
      linear-gradient(90deg, rgba(255, 255, 255, 0.25) 0%, rgba(255, 255, 255, 0) 40%, rgba(255, 255, 255, 0) 100%),
      linear-gradient(180deg,
        rgba(255, 255, 255, 0) 0%,
        #d6ecf9 8%,
        #a7d6f1 16%,
        #cfe9f8 22%,
        #6fb0e4 34%,
        #3f84d0 50%,
        #2f6fc0 62%,
        #4d95d8 74%,
        #7cc0ea 86%,
        #a9dbf3 100%);
  }
  .web-band {
    position: absolute;
    top: 1039px;
    left: 55px;
    right: 0;
    height: 51px;
    background: var(--navy);
    color: var(--white);
    font-weight: 600;
    font-size: 22px;
    display: flex;
    align-items: center;
    justify-content: center;
  }
</style>
</head>
<body>
  <main class="pylon">
    <div class="brand">
      <div class="brand-dot"></div>
      <div class="brand-name">Tailbright<br>Vethaus</div>
    </div>

    <h1 class="headline">Biegen Sie ein,<br>dann biegen wir<br>es hin!</h1>

    <div class="photo" role="img" aria-label="Foto eines blauen Stethoskops auf einer spiegelnden Fläche"></div>

    <div class="web-band">www.tailbright-vethaus.at</div>
  </main>
</body>
</html>
```